Kestrada LLC, needs a web page no more than 5 pages (for now)

Kestrada is a general contractor. Our services include general contracting, design-build construction, disaster recovery and environmental remediation. Our main clients are PMX, TQ, State and Local Gov't Agencies, Hospitals and Schools. Kestrada is also a SDVOSB.

```html
<!DOCTYPE html>
<html lang="en">
<head>
<meta charset="utf-8">
<title>Kestrada LLC — General Contractor</title>
<link href="https://fonts.googleapis.com/css2?family=Montserrat:wght@400;500;600;700;800&family=Roboto:wght@400;500;700&display=swap" rel="stylesheet">
<style>
:root{
  --gold:#b07c3b;
  --gold-light:#e6a73c;
  --gold-soft:#e9b457;
  --ink:#141414;
  --text:#555;
  --muted:#8a8a8a;
  --white:#fff;
  --line:#d9d9d9;
  --footer-bg:#f6f6f6;
}
*{margin:0;padding:0;box-sizing:border-box}
html,body{width:1200px;height:3798px;overflow:hidden}
body{font-family:"Roboto",sans-serif;color:var(--ink);background:var(--white);position:relative}
.abs{position:absolute}
.photo{position:absolute;display:block}
.btn{position:absolute;display:flex;align-items:center;justify-content:center;gap:14px;font-family:"Roboto",sans-serif;font-weight:700;font-size:14px;text-transform:uppercase;letter-spacing:.2px;border:2px solid var(--gold);color:var(--gold);background:transparent}
.btn svg{width:26px;height:10px}
.eyebrow{position:absolute;font-family:"Montserrat",sans-serif}
.eyebrow .ghost{font-size:60px;font-weight:800;color:rgba(0,0,0,.06);letter-spacing:1px;line-height:1}
.eyebrow .tag{position:absolute;font-size:17px;color:var(--gold);font-weight:500;white-space:nowrap}
.heading{position:absolute;font-family:"Montserrat",sans-serif;font-weight:700;text-transform:uppercase;font-size:36px;line-height:1.3;color:var(--ink)}

/* header */
.site-header{position:absolute;left:0;top:0;width:1200px;height:88px;background:var(--white)}
.brand{position:absolute;left:144px;top:22px;display:flex;align-items:center;gap:10px;font-family:"Montserrat",sans-serif;font-weight:700;font-size:26px;color:var(--gold)}
.brand .dot{width:16px;height:16px;border-radius:50%;background:var(--gold)}
.topbar{position:absolute;top:0;left:718px;height:30px;display:flex;font-size:13px;color:var(--white)}
.topbar .phone{width:165px;background:var(--gold);display:flex;align-items:center;justify-content:center;gap:7px;clip-path:polygon(8% 0,100% 0,100% 100%,0 100%)}
.topbar .mail{width:172px;background:#d6d6d6;color:var(--ink);display:flex;align-items:center;justify-content:center;gap:8px;clip-path:polygon(0 0,100% 0,92% 100%,0 100%)}
.topbar svg{width:12px;height:12px}
.main-nav{position:absolute;top:56px;right:145px;display:flex;gap:46px;font-size:14px;font-weight:500;text-transform:uppercase}
.main-nav a{color:var(--ink);text-decoration:none}
.main-nav a.active{color:var(--gold-light)}

/* hero */
.hero{position:absolute;left:0;top:88px;width:1200px;height:572px;overflow:hidden}
.hero .photo{inset:0;background:linear-gradient(180deg,#8fa3ba 0%,#a7aeb3 30%,#7c7a76 60%,#5e5a55 100%)}
.hero .shade{position:absolute;inset:0;background:rgba(20,20,25,.35)}
.hero h1{position:absolute;top:122px;left:0;width:1200px;text-align:center;font-family:"Montserrat",sans-serif;font-weight:800;font-size:48px;line-height:62px;color:var(--white);text-transform:uppercase}
.hero p{position:absolute;top:252px;left:0;width:1200px;text-align:center;font-size:19px;line-height:33px;color:var(--white)}
.hero .btn{left:508px;top:348px;width:183px;height:46px;background:var(--gold);color:var(--white);border-color:var(--gold-soft);font-size:15px;text-transform:uppercase}
.hero .arrow{position:absolute;top:269px;width:36px;height:36px;border-radius:50%;background:rgba(0,0,0,.75);display:flex;align-items:center;justify-content:center}
.hero .arrow svg{width:12px;height:12px}

/* about */
.about-text{position:absolute;left:144px;top:884px;width:440px;font-size:13.5px;line-height:24px;color:var(--text)}
.about-text p+p{margin-top:6px}
.about .frame-gold{position:absolute;left:680px;top:766px;width:406px;height:399px;background:var(--gold-soft)}
.about .frame-grey{position:absolute;left:666px;top:745px;width:405px;height:400px;background:#eee}
.about .photo{left:650px;top:730px;width:405px;height:399px;background:linear-gradient(160deg,#5d9ad6 0%,#7fb1de 45%,#3a4a6c 75%,#2a3450 100%)}

/* services */
.services{position:absolute;left:0;top:1229px;width:1200px;height:920px;background:var(--gold)}
.services .ghost-word{position:absolute;top:50px;left:502px;font-family:"Montserrat",sans-serif;font-weight:800;font-size:58px;color:rgba(255,255,255,.22)}
.services .tag{position:absolute;top:72px;left:675px;font-family:"Montserrat",sans-serif;font-size:18px;color:var(--white);font-weight:500}
.services h2{position:absolute;top:122px;left:0;width:1200px;text-align:center;font-family:"Montserrat",sans-serif;font-weight:700;font-size:35px;color:var(--white);text-transform:uppercase}
.card{position:absolute;width:449px;height:320px;overflow:hidden;color:var(--white);text-align:center}
.card .photo{inset:0}
.card .fade{position:absolute;inset:0;background:linear-gradient(180deg,rgba(0,0,0,0) 35%,rgba(0,0,0,.85) 82%,#000 100%)}
.card h3{position:absolute;left:0;right:0;top:200px;font-size:17px;font-weight:500}
.card p{position:absolute;left:28px;right:28px;top:230px;font-size:13.5px;line-height:23px}
.card .more{position:absolute;left:0;right:0;top:287px;font-size:13px;font-weight:700;color:var(--gold-light);display:flex;justify-content:center;align-items:center;gap:6px}
.card .more span.ic{width:12px;height:12px;border-radius:50%;background:var(--gold-light);display:inline-flex;align-items:center;justify-content:center}

/* projects */
.project{position:absolute;top:2349px;width:216px;height:216px}

/* certifications */
.cert .photo{left:0;top:2646px;width:556px;height:457px;background:linear-gradient(120deg,#d8d4cf 0%,#bfa88a 40%,#3f4a5e 70%,#c9c6c2 100%)}
.cert .lead{position:absolute;left:635px;top:2856px;width:430px;font-size:15.5px;line-height:25px;color:var(--ink);font-weight:500}
.cert .body{position:absolute;left:635px;top:2914px;width:430px;font-size:13.5px;line-height:24px;color:var(--text)}

/* cta */
.cta{position:absolute;left:0;top:3184px;width:1200px;height:318px;background:var(--gold);text-align:center}
.cta h2{position:absolute;top:62px;left:0;width:1200px;font-family:"Montserrat",sans-serif;font-weight:700;font-size:38px;line-height:64px;color:var(--white);text-transform:uppercase}
.cta .btn{left:463px;top:209px;width:274px;height:46px;border-color:var(--white);color:var(--white)}

/* footer */
.site-footer{position:absolute;left:0;top:3502px;width:1200px;height:296px;background:var(--footer-bg)}
.footer-brand{position:absolute;left:144px;top:100px;display:flex;align-items:center;gap:12px;font-family:"Montserrat",sans-serif;font-weight:700;font-size:34px;color:var(--gold)}
.footer-brand .dot{width:22px;height:22px;border-radius:50%;background:var(--gold)}
.fcol{position:absolute;top:62px}
.fcol h4{font-family:"Montserrat",sans-serif;font-weight:500;font-size:16px;color:var(--ink);text-transform:uppercase;margin-bottom:8px}
.fcol ul{list-style:none}
.fcol li{font-size:13px;line-height:20.6px;color:var(--text);display:flex;align-items:center;gap:10px}
.fcol li::before{content:"»";color:var(--gold);font-size:14px}
.socials{position:absolute;left:609px;top:168px;display:flex;gap:9px}
.socials span{width:28px;height:28px;border-radius:50%;border:1.5px solid var(--gold)}
.socials span.on{background:var(--gold)}
.contact li{display:flex;align-items:flex-start;gap:12px;font-size:13px;line-height:19px;color:var(--text);margin-bottom:18px}
.contact li::before{content:none}
.contact .ic{flex:none;width:24px;height:24px;border-radius:50%;border:1.5px solid var(--line);display:flex;align-items:center;justify-content:center;margin-top:-3px}
.contact .ic svg{width:11px;height:11px}
.footer-rule{position:absolute;left:144px;top:247px;width:911px;height:1px;background:var(--line)}
.copyright{position:absolute;top:265px;left:0;width:1200px;text-align:center;font-size:12.5px;color:var(--text)}
</style>
</head>
<body>

<header class="site-header">
  <div class="brand"><span class="dot"></span>Kestrada</div>
  <div class="topbar">
    <div class="phone"><svg viewBox="0 0 24 24" fill="#fff"><path d="M6.6 10.8a15 15 0 006.6 6.6l2.2-2.2a1 1 0 011-.25 11.4 11.4 0 003.6.57 1 1 0 011 1V20a1 1 0 01-1 1A17 17 0 013 4a1 1 0 011-1h3.5a1 1 0 011 1c0 1.25.2 2.45.57 3.57a1 1 0 01-.25 1z"/></svg>+1-555-014-2270</div>
    <div class="mail"><svg viewBox="0 0 24 24" fill="#141414"><path d="M2 5h20v14H2z" opacity=".9"/><path d="M2 5l10 8 10-8" stroke="#d6d6d6" stroke-width="2" fill="none"/></svg>hello@kestradabuild.com</div>
  </div>
  <nav class="main-nav">
    <a class="active" href="#">Home</a><a href="#">About Us</a><a href="#">Services</a><a href="#">Certifications</a><a href="#">Contact Us</a>
  </nav>
</header>

<section class="hero">
  <div class="photo" role="img" aria-label="Contractor in hard hat and suit overlooking a collapsed building site"></div>
  <div class="shade"></div>
  <h1>Ready for the worst,<br>delivering the best</h1>
  <p>Rusted General Contractor For Government, Healthcare, and<br>Institutional Projects Across The United States</p>
  <a class="btn" href="#">Get Started <svg viewBox="0 0 26 10"><path d="M0 5h24M19 1l5 4-5 4" stroke="#fff" stroke-width="1.6" fill="none"/></svg></a>
  <span class="arrow" style="left:91px"><svg viewBox="0 0 12 12"><path d="M8 1L3 6l5 5" stroke="#fff" stroke-width="2" fill="none"/></svg></span>
  <span class="arrow" style="left:1071px"><svg viewBox="0 0 12 12"><path d="M4 1l5 5-5 5" stroke="#fff" stroke-width="2" fill="none"/></svg></span>
</section>

<section class="about">
  <div class="eyebrow" style="left:144px;top:764px"><span class="ghost">WHO</span><span class="tag" style="left:132px;top:18px">We Are</span></div>
  <h2 class="heading" style="left:144px;top:818px">About Kestrada</h2>
  <div class="about-text">
    <p>Duis aute irure dolor in reprehenderit in voluptate velit esse cillum dolore eu fugiat nulla pariatur. Excepteur sint occaecat cupidatat non proident, sunt in culpa qui officia deserunt mollit anim id est laborum.</p>
    <p>Nemo enim ipsam voluptatem quia voluptas sit aspernatur aut odit aut fugit, sed quia consequuntur magni dolores</p>
  </div>
  <a class="btn" href="#" style="left:144px;top:1032px;width:168px;height:44px">Read More <svg viewBox="0 0 26 10"><path d="M0 5h24M19 1l5 4-5 4" stroke="#b07c3b" stroke-width="1.6" fill="none"/></svg></a>
  <div class="frame-gold"></div>
  <div class="frame-grey"></div>
  <div class="photo" role="img" aria-label="Smiling engineer in hard hat holding a tablet in front of a building under construction"></div>
</section>

<section class="services">
  <span class="ghost-word">WHAT</span><span class="tag">We Do</span>
  <h2>Experience our services excellence</h2>

  <article class="card" style="left:144px;top:198px">
    <div class="photo" role="img" aria-label="Construction team in hard hats meeting with clients" style="background:linear-gradient(135deg,#cfc9c0,#7d7a74 60%,#3a3a3a)"></div>
    <div class="fade"></div>
    <h3>General Contracting</h3>
    <p>Lorem ipsum dolor sit amet, consectetur adipiscing elit, eiusmod tempor incididunt ut labore et dolore.</p>
    <div class="more">Read More <span class="ic"><svg width="6" height="8" viewBox="0 0 6 8"><path d="M1 1l3 3-3 3" stroke="#000" stroke-width="1.5" fill="none"/></svg></span></div>
  </article>

  <article class="card" style="left:607px;top:198px">
    <div class="photo" role="img" aria-label="Architect reviewing floor plans on a computer screen" style="background:linear-gradient(135deg,#6c6a66,#d9d7d3 50%,#3b3b3b)"></div>
    <div class="fade"></div>
    <h3>Design-Build Construction</h3>
    <p>Lorem ipsum dolor sit amet, consectetur adipiscing elit, eiusmod tempor incididunt ut labore et dolore.</p>
    <div class="more">Read More <span class="ic"><svg width="6" height="8" viewBox="0 0 6 8"><path d="M1 1l3 3-3 3" stroke="#000" stroke-width="1.5" fill="none"/></svg></span></div>
  </article>

  <article class="card" style="left:144px;top:532px">
    <div class="photo" role="img" aria-label="Recovery crew in safety vests clearing debris near damaged homes" style="background:linear-gradient(160deg,#8aa3c2,#b8b29e 45%,#5a4d3e)"></div>
    <div class="fade"></div>
    <h3>Disaster Recovery</h3>
    <p>Lorem ipsum dolor sit amet, consectetur adipiscing elit, eiusmod tempor incididunt ut labore et dolore.</p>
    <div class="more">Read More <span class="ic"><svg width="6" height="8" viewBox="0 0 6 8"><path d="M1 1l3 3-3 3" stroke="#000" stroke-width="1.5" fill="none"/></svg></span></div>
  </article>

  <article class="card" style="left:607px;top:532px">
    <div class="photo" role="img" aria-label="Workers in protective suits at an industrial storage tank facility" style="background:linear-gradient(160deg,#d3d6d9,#b9b9a8 50%,#5b5a4e)"></div>
    <div class="fade"></div>
    <h3>Environmental Remediation</h3>
    <p>Lorem ipsum dolor sit amet, consectetur adipiscing elit, eiusmod tempor incididunt ut labore et dolore.</p>
    <div class="more">Read More <span class="ic"><svg width="6" height="8" viewBox="0 0 6 8"><path d="M1 1l3 3-3 3" stroke="#000" stroke-width="1.5" fill="none"/></svg></span></div>
  </article>
</section>

<section class="projects">
  <div class="eyebrow" style="left:144px;top:2222px"><span class="ghost">OUR</span><span class="tag" style="left:113px;top:20px">Portfolio</span></div>
  <h2 class="heading" style="left:144px;top:2276px">Featured Projects</h2>
  <a class="btn" href="#" style="left:831px;top:2270px;width:224px;height:43px">View All Projects <svg viewBox="0 0 26 10"><path d="M0 5h24M19 1l5 4-5 4" stroke="#b07c3b" stroke-width="1.6" fill="none"/></svg></a>
  <div class="photo project" style="left:144px;background:linear-gradient(160deg,#8d8d8d,#c46a3c 45%,#555)" role="img" aria-label="Rescue workers in orange gear on rubble"></div>
  <div class="photo project" style="left:376px;background:linear-gradient(160deg,#9cc1d8,#e7ecef 45%,#6a7a5a)" role="img" aria-label="Technician in protective suit sampling water"></div>
  <div class="photo project" style="left:608px;background:linear-gradient(160deg,#b9c2c8,#e0a43a 40%,#8fbf3a 80%)" role="img" aria-label="Engineer reviewing plans on a tablet"></div>
  <div class="photo project" style="left:840px;background:linear-gradient(160deg,#e3e3e3,#d98a4a 45%,#50607a)" role="img" aria-label="Contractor shaking hands with clients"></div>
  <div class="photo project" style="left:1072px;background:linear-gradient(160deg,#bfc3c6,#eeeeee 50%,#6b7a8a)" role="img" aria-label="Team reviewing blueprints at a table"></div>
</section>

<section class="cert">
  <div class="photo" role="img" aria-label="Contractor in hard hat shaking hands with a client on site"></div>
  <div class="eyebrow" style="left:635px;top:2680px"><span class="ghost">OUR</span><span class="tag" style="left:103px;top:22px">Accreditations</span></div>
  <h2 class="heading" style="left:635px;top:2738px">Certifications and<br>Credentials</h2>
  <p class="lead">Duis aute irure dolor in reprehenderit in voluptate velit esse cillum dolore eu fugiat nulla pariatur excepteur.</p>
  <p class="body">Lorem ipsum dolor sit amet, consectetur adipiscing elit, do eiusmod tempor incididunt ut labore et dolore magna aliqua. Ut enim ad minim veniam, quis nostrud exercitation ullamco laboris.</p>
  <a class="btn" href="#" style="left:634px;top:3013px;width:223px;height:43px">View Certificates <svg viewBox="0 0 26 10"><path d="M0 5h24M19 1l5 4-5 4" stroke="#b07c3b" stroke-width="1.6" fill="none"/></svg></a>
</section>

<section class="cta">
  <h2>Ready to start your project?<br>Let’s build together</h2>
  <a class="btn" href="#">Request a Consultation <svg viewBox="0 0 26 10"><path d="M0 5h24M19 1l5 4-5 4" stroke="#fff" stroke-width="1.6" fill="none"/></svg></a>
</section>

<footer class="site-footer">
  <div class="footer-brand"><span class="dot"></span>Kestrada</div>
  <div class="fcol" style="left:421px">
    <h4>Quick Links</h4>
    <ul><li>Home</li><li>About Us</li><li>Services</li><li>Projects</li><li>Certifications</li><li>Contact</li></ul>
  </div>
  <div class="fcol" style="left:609px">
    <h4>Other Links</h4>
    <ul><li>Term of Services</li><li>Site Map</li><li>Privacy Policy</li></ul>
  </div>
  <div class="socials"><span></span><span class="on"></span><span></span><span></span></div>
  <div class="fcol contact" style="left:822px">
    <h4>Contact Us</h4>
    <ul>
      <li><span class="ic"><svg viewBox="0 0 24 24" fill="#b07c3b"><path d="M6.6 10.8a15 15 0 006.6 6.6l2.2-2.2a1 1 0 011-.25 11.4 11.4 0 003.6.57 1 1 0 011 1V20a1 1 0 01-1 1A17 17 0 013 4a1 1 0 011-1h3.5a1 1 0 011 1c0 1.25.2 2.45.57 3.57a1 1 0 01-.25 1z"/></svg></span>+1-555-014-2270</li>
      <li><span class="ic"><svg viewBox="0 0 24 24"><rect x="2" y="5" width="20" height="14" fill="#b07c3b"/><path d="M2 5l10 8 10-8" stroke="#fff" stroke-width="2" fill="none"/></svg></span>hello@kestradabuild.com</li>
      <li><span class="ic"><svg viewBox="0 0 24 24" fill="#b07c3b"><path d="M12 2a7 7 0 00-7 7c0 5 7 13 7 13s7-8 7-13a7 7 0 00-7-7zm0 9.5A2.5 2.5 0 1112 6.5a2.5 2.5 0 010 5z"/></svg></span>10 Duis aute irure dolor in reprehen<br>derit in voluptate 5263,USA</li>
    </ul>
  </div>
  <div class="footer-rule"></div>
  <p class="copyright">© 2025 &nbsp;Kestrada &nbsp;| &nbsp;All Rights Reserved</p>
</footer>

</body>
</html>
```